Create a premium soap bar box bar design for an all-natural, men's skincare brand.

We are launching a men’s premium, natural soap bar and skincare business. To start, we will be launching cold-press, all-natural soap bars with a few additional products such as lotions. We plan to expand our line into additional skincare products such as face exfoliants, moisturizers and cleansers that target basic needs such as anti-aging, clarifying and hydrating.

Our target audience is men ages 25-50, with a secondary audience of male teens. Our target audience are mid to high income, professionals that live in more urban areas, but enjoy being active outdoors after work and on the weekends. Our target audience are hard workers, humble and want to enjoy all that life has to offer – whether that’s on top of a mountain or an ocean wave. They hike, bike, skateboard, surf or any other sport that gets them outside. They are husbands, brothers and fathers – there for their family and friends.

Our brand is sophisticated, adventurous and has a sense of humor. Many of our competitors either focus on the rugged outdoors or are more pretentious. We are in-between. We are free spirited and love the fresh air. Our products are trustworthy with no toxic chemicals or harsh ingredients. We are all-natural and provide high-quality, premium products that our audience expects and deserves.

Target Market(s)

Men, ages 25-54 who are high-earning professionals, yet enjoy getting outdoors and being active on the weekends - hiking, biking, surfing, skateboarding and more.

Industry/Entity Type

Men's skincare

Font styles to use
Sans Serif

Requirements
Must have
• See attachments
Nice to have
• We would prefer to a have a premium, slightly more modern looking design that will appeal to our target audience and slightly higher price point.
Should not have
• Please do not include an icon for the fragrance, i.e. cinnamon sticks. However, we do need some differentiation for the fragrance, i.e. color, etc. as it will be on the shelf with other fragrances.

```html
<!DOCTYPE html>
<html lang="en">
<head>
<meta charset="utf-8">
<title>Hale Marlow – Cinnamon Bark Soap Box</title>
<link href="https://fonts.googleapis.com/css2?family=Kumbh+Sans:wght@400;500;600;700&display=swap" rel="stylesheet">
<style>
  :root {
    --page: #ffffff;
    --kraft: #b5a08a;
    --kraft-side: #d9c9b6;
    --band: #17191e;
    --band-edge: #a8927a;
    --ink-light: #ffffff;
  }
  * { box-sizing: border-box; margin: 0; padding: 0; }
  html, body { width: 1200px; height: 1000px; overflow: hidden; background: var(--page); }
  body { position: relative; font-family: "Kumbh Sans", sans-serif; color: var(--ink-light); }

  .box { position: absolute; left: 290px; width: 596px; height: 390px; display: flex; }
  .box--front { top: 68px; }
  .box--back { top: 550px; }

  .side-panel {
    width: 66px; height: 100%; background: var(--kraft-side);
    display: flex; flex-direction: column; align-items: center;
    padding: 14px 6px; text-align: center;
  }
  .side-panel--info { padding-top: 82px; padding-bottom: 44px; }
  .main-panel { position: relative; flex: 1; background: var(--kraft); }

  .band {
    position: absolute; top: 0; bottom: 0; left: 148px; width: 234px;
    background: var(--band-edge);
  }
  .band__core {
    position: absolute; top: 0; bottom: 0; left: 15px; right: 15px;
    background: var(--band);
    display: flex; flex-direction: column; align-items: center; text-align: center;
  }

  /* Front */
  .brand { margin-top: 142px; display: flex; align-items: center; gap: 8px; }
  .brand__mark { width: 10px; height: 10px; background: var(--ink-light); }
  .brand__name { font-size: 20px; font-weight: 600; letter-spacing: 0; }
  .product-name { margin-top: 52px; font-size: 20px; font-weight: 600; line-height: 1.15; letter-spacing: .3px; }
  .product-type { margin-top: 12px; font-size: 13px; font-weight: 500; }
  .net-weight { margin-top: auto; margin-bottom: 20px; font-size: 13px; font-weight: 500; }

  .side-copy { font-size: 6px; line-height: 1.3; font-weight: 600; color: var(--ink-light); }
  .side-copy + .side-copy { margin-top: 10px; }
  .recycle { margin-top: 20px; }
  .distributor { margin-top: auto; font-size: 5px; line-height: 1.3; font-weight: 600; }

  /* Back */
  .headline { margin-top: 60px; font-size: 19px; font-weight: 600; line-height: 1.2; }
  .story { margin-top: 24px; padding: 0 20px; font-size: 10.5px; line-height: 1.62; font-weight: 500; }
  .story strong { font-size: 14px; font-weight: 600; }
  .site-link { margin-top: 18px; font-size: 6.5px; font-weight: 500; }

  .claims { list-style: none; margin-top: 62px; display: flex; flex-direction: column; align-items: center; gap: 16px; }
  .claim { display: flex; flex-direction: column; align-items: center; }
  .claim__icon { width: 24px; height: 24px; border-radius: 50%; background: var(--ink-light); margin-bottom: 4px; }
  .claim__label { font-size: 8px; line-height: 1.15; font-weight: 600; }
</style>
</head>
<body>

  <section class="box box--front" aria-label="Box front">
    <aside class="side-panel side-panel--info">
      <p class="side-copy">Directions: Lather, rinse and repeat.</p>
      <p class="side-copy">Ingredients: Vegetable Oil Blend (Olive Oil, Organic Sustainable Palm Oil, Coconut Oil), Shea Butter, Sunflower Oil, Water, Sodium Hydroxide, Beeswax, Cinnamon Essential Oil, Honey, Ground Cinnamon.</p>
      <svg class="recycle" width="22" height="20" viewBox="0 0 22 20" aria-hidden="true">
        <g fill="none" stroke="#fff" stroke-width="2" stroke-linejoin="round">
          <path d="M11 2 L19 16 L3 16 Z"/>
        </g>
      </svg>
      <p class="distributor">Distributed by Hale Marlow, Columbus, Ohio</p>
    </aside>
    <div class="main-panel">
      <div class="band">
        <div class="band__core">
          <div class="brand">
            <span class="brand__mark"></span>
            <span class="brand__name">Hale Marlow</span>
          </div>
          <h1 class="product-name">CINNAMON<br>BARK</h1>
          <p class="product-type">Men’s Natural Soap</p>
          <p class="net-weight">5 Oz. Bar</p>
        </div>
      </div>
    </div>
  </section>

  <section class="box box--back" aria-label="Box back">
    <aside class="side-panel">
      <ul class="claims">
        <li class="claim"><span class="claim__icon"></span><span class="claim__label">Made in<br>USA</span></li>
        <li class="claim"><span class="claim__icon"></span><span class="claim__label">No harsh<br>chemicals</span></li>
        <li class="claim"><span class="claim__icon"></span><span class="claim__label">Sustainably<br>sourced</span></li>
        <li class="claim"><span class="claim__icon"></span><span class="claim__label">Hand-<br>crafted</span></li>
      </ul>
    </aside>
    <div class="main-panel">
      <div class="band">
        <div class="band__core">
          <h2 class="headline">Real Ingredients<br>for Real Guys.</h2>
          <p class="story">Bring the outdoors in using real, natural ingredients on your skin. Traditional bar soap contains harsh chemical ingredients that can be harmful to you and the environment. Lather up with Hale Marlow’s handcrafted, all-natural soap and <strong>feel the difference.</strong></p>
          <p class="site-link">Check out all our products at halemarlow.com</p>
        </div>
      </div>
    </div>
  </section>

</body>
</html>
```